Animal Horse & Bedding Company Needs a Website Coded & Designed

We need a website for a new animal bedding and feed company that is visually grabbing and vibrant. We would like to see a website that displays trust, quality and confidence. Needs to be responsive and mobile friendly for all browsers and coded for both Android & IOS. SEO is also important.

Joomla or Wordpress – must be both desktop and mobile friendly with fast page load speed. Need the ability to edit ourselves in Wordpress or Joomla.

Full details attached below with some layout and content ideas.

Coding

Coded - Design and coding required

Number of Pages Required

5+ page

Font styles to use
Sans Serif

Requirements
Must have
• Needs to be responsive and mobile friendly for all browsers and coded for both Android & IOS. SEO is also important.

Wordpress – must be both desktop and mobile friendly with fast page load speed. Need the ability to edit ourselves in Wordpress.

Logo Colours:
Dark Brown
CMYK: 50 / 70 / 80 / 70
Pantone: 4625C

Orange
CMYK: 0 / 50 / 100 / 0
Pantone: 144C
Nice to have
• Use picture of building attached and super impose logo on building.

```html
<!DOCTYPE html>
<html lang="en">
<head>
<meta charset="utf-8">
<title>Hayfield Supply – Bedding &amp; Feed</title>
<link href="https://fonts.googleapis.com/css2?family=Oswald:wght@300;400&family=Roboto:wght@400;500;700&display=swap" rel="stylesheet">
<style>
:root{
  --orange:#ef9b0f;
  --brown:#3a2318;
  --ink:#222;
  --text:#666;
  --white:#fff;
  --footer:#4f4f4f;
}
*{box-sizing:border-box;margin:0;padding:0}
html,body{width:1200px;height:3621px;overflow:hidden}
body{position:relative;font-family:Roboto,Arial,sans-serif;color:var(--ink);background:var(--white)}
.abs{position:absolute}
.heading-font{font-family:Oswald,"Arial Narrow",sans-serif;font-weight:300;text-transform:uppercase}
/* header */
.site-header{position:absolute;left:0;top:0;width:1200px;height:97px;background:var(--white);border-bottom:1px solid #e6e6e6}
.brand{position:absolute;left:111px;top:30px;display:flex;align-items:center;gap:10px}
.brand-dot{width:18px;height:18px;border-radius:50%;background:var(--orange)}
.brand-name{font-family:Oswald,sans-serif;font-weight:400;font-size:24px;letter-spacing:1px;color:var(--brown);text-transform:uppercase}
.main-nav{position:absolute;top:40px;left:0;font-size:13px;font-weight:700}
.main-nav a{position:absolute;white-space:nowrap;color:#111;text-decoration:none}
.main-nav a.active{color:var(--orange)}
.btn{position:absolute;display:flex;align-items:center;justify-content:center;gap:8px;border-radius:30px;font-size:13px;font-weight:700;text-transform:uppercase;color:var(--white);background:var(--orange);box-shadow:0 0 0 3px var(--white),0 0 0 5px var(--orange)}
.btn.dark{background:var(--brown);box-shadow:0 0 0 3px var(--white),0 0 0 5px var(--brown)}
.btn.outline-dark{box-shadow:0 0 0 3px var(--white),0 0 0 5px var(--brown)}
.btn svg{width:13px;height:13px}
/* hero */
.hero{position:absolute;left:0;top:97px;width:1200px;height:537px;background:linear-gradient(180deg,#c9d6d0 0%,#9fb489 28%,#8a9a3a 50%,#a1a52f 75%,#8a8b2a 100%)}
.hero-title{position:absolute;left:0;width:1200px;top:100px;text-align:center;color:var(--white);font-family:Oswald,sans-serif;font-weight:300;font-size:42px;line-height:60px;text-transform:uppercase;text-shadow:0 2px 6px rgba(0,0,0,.35)}
.hero-dots{position:absolute;top:447px;left:572px;display:flex;gap:4px}
.hero-dots span{width:9px;height:9px;border-radius:50%;background:var(--white)}
.hero-dots span.on{background:transparent;border:2px solid var(--white)}
/* welcome */
.welcome{position:absolute;left:0;top:634px;width:1200px;height:617px;background:linear-gradient(90deg,#f3f3f3 0%,#fafafa 50%,#f1f0ee 100%);border-bottom:1px solid #e8e8e8}
.welcome-art{position:absolute;left:148px;top:76px;width:337px;height:450px;border-radius:45% 45% 50% 50%;background:radial-gradient(circle at 50% 55%,#f3dcc0 0%,#d9a874 45%,#b98552 70%,#f5f5f5 72%)}
.eyebrow{font-family:Oswald,sans-serif;font-weight:300;font-size:16px;text-transform:uppercase;color:#222}
.section-title{font-family:Oswald,sans-serif;font-weight:300;font-size:38px;text-transform:uppercase;color:var(--orange);line-height:1}
.rule{width:32px;height:2px;background:#333}
.welcome-text{position:absolute;left:573px;top:211px;width:495px;font-size:14px;line-height:28.3px;color:var(--text)}
/* services */
.services-head{position:absolute;left:0;width:1200px;text-align:center}
.services{position:absolute;left:0;top:1480px;width:1200px;height:340px}
.service{position:absolute;width:280px;text-align:center;color:var(--white)}
.service h3{font-size:15px;font-weight:700;text-transform:uppercase;margin-top:10px}
.service .srule{width:36px;height:2px;background:var(--white);margin:16px auto 14px}
.service p{font-size:15px;line-height:26px;padding:0 12px}
.service svg{display:block;margin:0 auto;width:76px;height:78px}
/* benefits */
.benefit{position:absolute;top:1933px;width:600px;height:537px;color:var(--white)}
.benefit.bedding{left:0;background:linear-gradient(160deg,#7a5a4c,#8d6a5b 50%,#a07a68)}
.benefit.feed{left:600px;background:linear-gradient(160deg,#eca43b,#f0b04a 50%,#e7a136)}
.benefit h2{position:absolute;left:110px;top:68px;font-family:Oswald,sans-serif;font-weight:300;font-size:26px;text-transform:uppercase}
.benefit ul{position:absolute;left:110px;top:126px;list-style:none;font-size:15px}
.benefit li{height:34.4px;display:flex;gap:18px;align-items:flex-start}
.benefit li svg{width:14px;height:14px;margin-top:2px;flex:none}
.benefit li.cont{padding-left:40px}
/* why */
.why-photo{position:absolute;left:644px;top:2593px;width:446px;height:298px;background:var(--white);box-shadow:0 1px 6px rgba(0,0,0,.25);padding:4px}
.why-photo div{width:100%;height:100%;background:linear-gradient(180deg,#c9d3dc 0%,#aeb9c2 28%,#6f8a4a 30%,#8a8f5a 60%,#b2413a 62%,#8d8a62 75%,#99995f 100%)}
/* newsletter */
.newsletter{position:absolute;left:0;top:3021px;width:1200px;height:337px;background:linear-gradient(180deg,#3b3d3f 0%,#5b5a52 35%,#6c5c3f 65%,#8a5a2c 100%);color:var(--white);text-align:center}
.field{position:absolute;top:215px;height:49px;background:var(--white);border-radius:25px;display:flex;align-items:center;justify-content:space-between;padding:0 25px;font-size:14px;color:#888}
.field svg{width:14px;height:14px}
/* footer */
.site-footer{position:absolute;left:0;top:3358px;width:1200px;height:263px;background:var(--footer);color:var(--white);font-size:14px}
.site-footer h4{position:absolute;top:64px;font-size:13.5px;font-weight:700;text-transform:uppercase}
.fcol{position:absolute;top:98px;line-height:30px}
.social{position:absolute;top:119px;left:118px;display:flex;gap:10px}
.social span{width:34px;height:34px}
</style>
</head>
<body>

<header class="site-header">
  <div class="brand"><span class="brand-dot"></span><span class="brand-name">Hayfield Supply</span></div>
  <nav class="main-nav">
    <a class="active" style="left:453px">HOME</a>
    <a style="left:527px">ABOUT US</a>
    <a style="left:629px">FEED</a>
    <a style="left:696px">BEDDING</a>
    <a style="left:790px">CONTACT US</a>
  </nav>
  <a class="btn" style="left:935px;top:24px;width:148px;height:48px">Request Quote</a>
</header>

<section class="hero">
  <div role="img" aria-label="Horses grazing in a green pasture with hay bales and a wooden fence at sunset" style="position:absolute;inset:0"></div>
  <h1 class="hero-title">Your animal deserves the very best<br>in health and comfort to keep them healthy,<br>strong and happy</h1>
  <div class="hero-dots"><span></span><span></span><span class="on"></span><span></span><span></span></div>
</section>

<section class="welcome">
  <div class="welcome-art" role="img" aria-label="Horseshoe-framed illustration of a wheat stalk over a cosy pet bed"></div>
  <div class="abs eyebrow" style="left:573px;top:100px">Welcome to</div>
  <h2 class="abs section-title" style="left:573px;top:136px">Hayfield Supply</h2>
  <div class="abs rule" style="left:573px;top:187px"></div>
  <p class="welcome-text">Looking for the best bedding and feed for your horse, livestock or household pet look no further.&nbsp; We use premium locally sourced straw and hay in all of our products and are committed in providing quality products and service. Your animal deserves the very best in health and comfort to keep them healthy, strong and happy.&nbsp; Our products are designed for horses, livestock (goats, cattle and sheep), small caged animals (rabbits, guinea pigs and more). Hayfield Supply offers supply and delivery of fresh bedding as well as removal of waste bedding.</p>
  <a class="btn" style="left:575px;top:456px;width:155px;height:48px">Learn More
    <svg viewBox="0 0 16 16"><circle cx="8" cy="8" r="8" fill="#fff"/><path d="M5 8h6M8 5l3 3-3 3" stroke="#ef9b0f" stroke-width="2" fill="none"/></svg></a>
</section>

<div class="services-head" style="top:1348px"><div class="eyebrow">What we do</div></div>
<div class="services-head" style="top:1383px"><h2 class="section-title">Our Services</h2></div>
<div class="abs rule" style="left:584px;top:1434px"></div>

<div class="services">
  <svg class="abs" style="left:0;top:0" width="1200" height="340" viewBox="0 1480 1200 340">
    <g fill="none" stroke="#3a2318" stroke-width="3">
      <circle cx="308" cy="1651" r="163"/><circle cx="600" cy="1651" r="163"/><circle cx="891" cy="1651" r="163"/>
    </g>
    <g fill="#fff">
      <circle cx="308" cy="1651" r="161"/><circle cx="600" cy="1651" r="161"/><circle cx="891" cy="1651" r="161"/>
    </g>
    <circle cx="308" cy="1651" r="150" fill="#ef9b0f"/>
    <circle cx="891" cy="1651" r="150" fill="#ef9b0f"/>
    <circle cx="600" cy="1651" r="150" fill="#3a2318"/>
  </svg>
  <div class="service" style="left:168px;top:44px">
    <svg viewBox="0 0 76 78" fill="none" stroke="#fff" stroke-width="2.5"><circle cx="38" cy="30" r="24"/><circle cx="38" cy="30" r="16"/><path d="M38 20l3 7h7l-6 4 2 7-6-4-6 4 2-7-6-4h7z"/><path d="M24 48l-8 20 9-3 4 8 7-17M52 48l8 20-9-3-4 8-7-17"/></svg>
    <h3>Quality Guaranteed</h3><div class="srule"></div>
    <p>Grown for quality - 100% natural with no chemicals or additives</p>
  </div>
  <div class="service" style="left:460px;top:44px">
    <svg viewBox="0 0 76 78" fill="none" stroke="#fff" stroke-width="2.5"><path d="M38 18a16 16 0 0 0-9 29v8h18v-8a16 16 0 0 0-9-29z"/><path d="M30 61h16M32 67h12M36 73h4M38 2v8M14 12l6 6M62 12l-6 6M4 34h8M64 34h8"/></svg>
    <h3>Full Service Solution</h3><div class="srule"></div>
    <p>Grown for quality - 100% natural with no chemicals or additives</p>
  </div>
  <div class="service" style="left:751px;top:44px">
    <svg viewBox="0 0 76 78" fill="none" stroke="#fff" stroke-width="2.5"><rect x="10" y="6" width="44" height="64" rx="4"/><rect x="16" y="12" width="32" height="12"/><path d="M17 32h6v6h-6zM29 32h6v6h-6zM41 32h6v6h-6zM17 44h6v6h-6zM29 44h6v6h-6zM17 56h6v6h-6z"/><circle cx="56" cy="58" r="14" fill="#ef9b0f"/><path d="M60 52h-6a3 3 0 0 0 0 6h4a3 3 0 0 1 0 6h-6M56 48v4M56 64v4"/></svg>
    <h3>Convenient &amp; Cost Effective</h3><div class="srule"></div>
    <p>Grown for quality - 100% natural with no chemicals or additives</p>
  </div>
</div>

<section class="benefit bedding">
  <div role="img" aria-label="Pigs resting on straw bedding inside a barn" style="position:absolute;inset:0"></div>
  <h2>Benefits of Bedding</h2>
  <ul>
    <li><svg viewBox="0 0 16 16"><circle cx="8" cy="8" r="8" fill="#fff"/><path d="M5 8h6M8 5l3 3-3 3" stroke="#8d6a5b" stroke-width="2" fill="none"/></svg>100% Natural Chopped Straw</li>
    <li><svg viewBox="0 0 16 16"><circle cx="8" cy="8" r="8" fill="#fff"/><path d="M5 8h6M8 5l3 3-3 3" stroke="#8d6a5b" stroke-width="2" fill="none"/></svg>Low Dust</li>
    <li><svg viewBox="0 0 16 16"><circle cx="8" cy="8" r="8" fill="#fff"/><path d="M5 8h6M8 5l3 3-3 3" stroke="#8d6a5b" stroke-width="2" fill="none"/></svg>Chemical &amp; Additive Free</li>
    <li><svg viewBox="0 0 16 16"><circle cx="8" cy="8" r="8" fill="#fff"/><path d="M5 8h6M8 5l3 3-3 3" stroke="#8d6a5b" stroke-width="2" fill="none"/></svg>Clean &amp; Highly Absorbent</li>
    <li><svg viewBox="0 0 16 16"><circle cx="8" cy="8" r="8" fill="#fff"/><path d="M5 8h6M8 5l3 3-3 3" stroke="#8d6a5b" stroke-width="2" fill="none"/></svg>Cheaper than Wood Shavings</li>
    <li><svg viewBox="0 0 16 16"><circle cx="8" cy="8" r="8" fill="#fff"/><path d="M5 8h6M8 5l3 3-3 3" stroke="#8d6a5b" stroke-width="2" fill="none"/></svg>Economic – less used and less wasted</li>
    <li><svg viewBox="0 0 16 16"><circle cx="8" cy="8" r="8" fill="#fff"/><path d="M5 8h6M8 5l3 3-3 3" stroke="#8d6a5b" stroke-width="2" fill="none"/></svg>Environmentally Friendly –</li>
    <li class="cont">Recyclable &amp; Compostable</li>
  </ul>
  <a class="btn" style="left:112px;top:416px;width:206px;height:48px">Learn More Bedding
    <svg viewBox="0 0 16 16"><circle cx="8" cy="8" r="8" fill="#fff"/><path d="M5 8h6M8 5l3 3-3 3" stroke="#ef9b0f" stroke-width="2" fill="none"/></svg></a>
</section>

<section class="benefit feed">
  <div role="img" aria-label="Child in a sun hat feeding animals through a farm fence" style="position:absolute;inset:0"></div>
  <h2>Benefits of Feed</h2>
  <ul>
    <li><svg viewBox="0 0 16 16"><circle cx="8" cy="8" r="8" fill="#fff"/><path d="M5 8h6M8 5l3 3-3 3" stroke="#ef9b0f" stroke-width="2" fill="none"/></svg>100% Natural</li>
    <li><svg viewBox="0 0 16 16"><circle cx="8" cy="8" r="8" fill="#fff"/><path d="M5 8h6M8 5l3 3-3 3" stroke="#ef9b0f" stroke-width="2" fill="none"/></svg>Chemical &amp; Additive Free</li>
    <li><svg viewBox="0 0 16 16"><circle cx="8" cy="8" r="8" fill="#fff"/><path d="M5 8h6M8 5l3 3-3 3" stroke="#ef9b0f" stroke-width="2" fill="none"/></svg>Available in Pellets or Cubes</li>
    <li><svg viewBox="0 0 16 16"><circle cx="8" cy="8" r="8" fill="#fff"/><path d="M5 8h6M8 5l3 3-3 3" stroke="#ef9b0f" stroke-width="2" fill="none"/></svg>High Protein Content</li>
    <li><svg viewBox="0 0 16 16"><circle cx="8" cy="8" r="8" fill="#fff"/><path d="M5 8h6M8 5l3 3-3 3" stroke="#ef9b0f" stroke-width="2" fill="none"/></svg>Eliminate Waste In Feeding</li>
    <li><svg viewBox="0 0 16 16"><circle cx="8" cy="8" r="8" fill="#fff"/><path d="M5 8h6M8 5l3 3-3 3" stroke="#ef9b0f" stroke-width="2" fill="none"/></svg>Clean - Eliminates Dust From Feeding Baled Hay</li>
    <li><svg viewBox="0 0 16 16"><circle cx="8" cy="8" r="8" fill="#fff"/><path d="M5 8h6M8 5l3 3-3 3" stroke="#ef9b0f" stroke-width="2" fill="none"/></svg>Cost Effective</li>
    <li><svg viewBox="0 0 16 16"><circle cx="8" cy="8" r="8" fill="#fff"/><path d="M5 8h6M8 5l3 3-3 3" stroke="#ef9b0f" stroke-width="2" fill="none"/></svg>Convenient</li>
  </ul>
  <a class="btn dark" style="left:112px;top:416px;width:206px;height:48px">Learn More Feed
    <svg viewBox="0 0 16 16"><circle cx="8" cy="8" r="8" fill="#fff"/><path d="M5 8h6M8 5l3 3-3 3" stroke="#3a2318" stroke-width="2" fill="none"/></svg></a>
</section>

<div class="abs eyebrow" style="left:111px;top:2649px">Why choose us</div>
<h2 class="abs section-title" style="left:111px;top:2683px">Delivery in Canada &amp; USA</h2>
<div class="abs rule" style="left:111px;top:2735px"></div>
<p class="abs" style="left:111px;top:2757px;width:440px;font-size:14.5px;line-height:25.5px;color:var(--text)">Bulk materials are more economical, arrive loose, in a trailer so there is no plastic waste.&nbsp; This is a cheaper solution to bagged shavings.</p>
<div class="why-photo"><div role="img" aria-label="Aerial view of red farm buildings and fields under a cloudy sky"></div></div>

<section class="newsletter">
  <div role="img" aria-label="Cattle grazing in a valley below mountains at dusk" style="position:absolute;inset:0"></div>
  <div class="abs eyebrow" style="left:0;width:1200px;top:65px;color:#fff">Newsletter</div>
  <h2 class="abs" style="left:0;width:1200px;top:98px;font-family:Oswald,sans-serif;font-weight:300;font-size:36px;text-transform:uppercase">Join our Newsletter</h2>
  <div class="abs" style="left:584px;top:149px;width:32px;height:2px;background:#fff"></div>
  <div class="field" style="left:143px;width:328px"><span>Name</span><svg viewBox="0 0 16 16" fill="#666"><circle cx="8" cy="5" r="4"/><path d="M1 16c0-4 3-6 7-6s7 2 7 6z"/></svg></div>
  <div class="field" style="left:493px;width:328px"><span>Emaill Address</span><svg viewBox="0 0 16 16" fill="#666"><path d="M1 3h14v10H1z"/><path d="M1 3l7 6 7-6" stroke="#fff" fill="none"/></svg></div>
  <a class="btn" style="left:850px;top:215px;width:200px;height:49px;box-shadow:none">Learn More Bedding
    <svg viewBox="0 0 16 16"><circle cx="8" cy="8" r="8" fill="#fff"/><path d="M5 8h6M8 5l3 3-3 3" stroke="#ef9b0f" stroke-width="2" fill="none"/></svg></a>
</section>

<footer class="site-footer">
  <div class="brand" style="left:118px;top:58px"><span class="brand-dot"></span><span class="brand-name" style="color:#fff;font-size:21px">Hayfield Supply</span></div>
  <div class="social"><span style="background:#2f5ea8"></span><span style="background:#27a6e0"></span><span style="background:#d9241b"></span></div>
  <div class="abs" style="left:118px;top:188px;font-size:13px">© 2021 Hayfield Supply. All Rights Reserved.</div>

  <h4 style="left:412px">Opening Hours</h4>
  <div class="fcol" style="left:412px;line-height:26px;font-size:13.5px">Mon - Fri 09.00 AM - 08.00 PM<br>Sat &nbsp; - Sun 09.00 AM - 06.00 PM</div>

  <h4 style="left:686px">Contact Us</h4>
  <div class="fcol" style="left:687px;font-size:13.5px">214 Meadow Lane<br>United States<br>Mail &nbsp;: &nbsp;hello@hayfieldsupply.com<br>Tel &nbsp; &nbsp; : &nbsp;1 800 555 0142</div>

  <h4 style="left:977px">Menu</h4>
  <div class="fcol" style="left:977px;font-size:13.5px">» &nbsp;Home<br>» &nbsp;About<br>» &nbsp;Services<br>» &nbsp;Sitemap</div>
</footer>

</body>
</html>
```